Create Website for new company called "Verdale Lodge 37"

Verdale Lodge 37 is a new business situated in Southwestern Colorado. We are creating a business that will rent out spaces where clients can grow their own marijuana. Picture a large green house with partitioned spaces that are secured by a lock. Best way to envision this would be to think of a storage business that rents out storage rooms. The difference is that we will be having the units inside a green house ( for growing purposes) Picture a small area that is secured by locks, Picture an area that has the ability to provide state of the art security, cameras etc. We want to focus our efforts on professionals, blue collar workers and end users of marijuana. Our emphasis is in the area of assisting those whom wish to grow their own plants. We want to provide them a safe facility in which to do that. . Keep in mind that we also build custom grow rooms at clients homes and provide a grow pod (lease these) where a small grow unit will be delivered and picked up from our clients whom want to lease a unit for a short amount of time. We have a business card ( just designed) and will send that information to those whom express an interests in this project. We want to be able to sign people up for our services by entering an agreement and signing the agreement while on the internet. We want to provide our services to those whom consume recreational and medical marijuana. This site will need to gather information I.e email addresses so that we can followup with offers. This is a tremendous opportunity for the right designer. We will be creating many more websites as other states come on line and make marijuana legal to consume. Use the business card model for a point of reference of how we envision the concept. That is a business card we just recently printed. The hands and the plant is our logo so far. Open to suggestions. There will be three levels of service. Bronze, Silver, Gold or Platinum. We will also have a retail biz down the road but not at the present time.

Target Market(s)

Ages 21-60

Industry/Entity Type

Medical

Logo Text

Verdale Lodge 37.

Number of Pages Required

5+ page

Requirements
Must have
• Clean appearance not to busy , easily navigable from link to link, page to page. Must have ability down the road to enter into a contractual agreement via the website. Must use our provided logo and example of that is on our business card that will be uploaded here shortly. We would like to have the colors that are on the business card however if you have suggestions or color schemes that you want us to consider that is okay.
Nice to have
• Nice to have a animation of seed to weed and how clients can save a tremendous amount of money growing their own cannabis. Nice to have testimonial page or feedback page. Have a membership component to website,
Should not have
• No flashing lights, etc. Not to busy in terms of animations.

```html
<!DOCTYPE html>
<html lang="en">
<head>
<meta charset="utf-8">
<title>Verdale Lodge 37</title>
<link href="https://fonts.googleapis.com/css2?family=Raleway:wght@400;500;600;700&display=swap" rel="stylesheet">
<style>
:root{
  --orange:#c8742c;
  --nav:#4b4b4b;
  --footer:#3b3b3b;
  --text:#555;
  --heading:#3a3a3a;
  --green:#1f7d3c;
  --rule:#dcdcdc;
  --white:#fff;
}
*{margin:0;padding:0;box-sizing:border-box}
html,body{width:837px;height:1200px;overflow:hidden;background:var(--white)}
body{position:relative;font-family:'Raleway',sans-serif;color:var(--text)}
h1,h2,h3,h4{font-weight:400}
.abs{position:absolute}
.brand{left:92px;top:34px;display:flex;align-items:center;gap:8px;font-size:22px;font-weight:700;color:var(--heading);letter-spacing:-.3px}
.brand-mark{width:14px;height:14px;background:var(--orange)}
.follow{left:641px;top:16px;font-size:11px;color:#888}
.social{left:641px;top:38px;display:flex;gap:4px}
.social span{width:22px;height:22px;border-radius:50%}
.nav{left:0;top:81px;width:837px;height:39px;background:var(--nav)}
.nav a{position:absolute;top:0;height:39px;line-height:39px;font-size:9.5px;font-weight:500;color:var(--white);text-decoration:none}
.nav a.active{background:var(--orange);width:78px;text-align:center}
.hero{left:0;top:120px;width:837px;height:310px;
  background:
    radial-gradient(ellipse 220px 170px at 720px 300px,rgba(236,226,206,.95),rgba(236,226,206,0) 100%),
    radial-gradient(ellipse 260px 120px at 560px 290px,rgba(40,50,30,.55),rgba(40,50,30,0) 100%),
    radial-gradient(ellipse 300px 160px at 260px 170px,rgba(150,200,60,.55),rgba(150,200,60,0) 100%),
    linear-gradient(180deg,#b9c6c4 0%,#9fb19a 14%,#7fa34a 30%,#6a9a22 55%,#4f7f1a 80%,#556b2a 100%)}
.hero-arrow{width:44px;height:44px;border-radius:50%;background:rgba(60,60,60,.45);top:154px}
.hero-arrow svg{position:absolute;left:14px;top:14px}
.welcome{left:0;top:466px;width:837px;text-align:center;font-size:22px;color:var(--heading)}
.welcome b,.section-title b{font-weight:700}
.intro{left:100px;top:510px;width:637px;text-align:center;font-size:9.4px;line-height:17.5px}
.btn{left:379px;top:574px;width:82px;height:27px;line-height:27px;text-align:center;background:var(--orange);color:var(--white);font-size:9.5px;font-weight:500}
.rule{left:91px;width:655px;height:1px;background:var(--rule)}
.section-title{left:0;width:837px;text-align:center;font-size:20px;color:var(--heading)}
.section-title .accent{color:var(--orange);font-weight:700}
.pager{left:725px;display:flex;gap:2px}
.service-img{top:700px;width:202px;height:116px;border:3px solid #eee}
.service-name{top:830px;width:202px;text-align:center;font-size:11px;font-weight:500;color:var(--green)}
.service-text{top:851px;width:202px;text-align:center;font-size:9.4px;line-height:13px}
.post{top:981px;width:315px;height:111px;border:1px solid #ddd}
.avatar{left:13px;top:18px;width:37px;height:37px;border-radius:50%;background:linear-gradient(#9a9a9a,#cfcfcf)}
.post-title{left:62px;top:16px;font-size:13.5px;color:#333}
.post-text{left:62px;top:36px;width:245px;font-size:9.3px;line-height:17px}
.post-meta{left:62px;top:81px;font-size:8.4px;color:#444;display:flex;gap:9px;align-items:center}
.post-meta span{display:flex;align-items:center;gap:3px}
.footer{left:0;top:1133px;width:837px;height:67px;background:var(--footer)}
.copyright{left:93px;top:33px;font-size:9.3px;color:#eee}
.to-top{left:728px;top:27px;width:19px;height:19px;border-radius:50%;background:var(--white)}
</style>
</head>
<body>
<header>
  <div class="abs brand"><span class="brand-mark"></span>Verdale Lodge 37</div>
  <div class="abs follow">Follow Us</div>
  <div class="abs social" aria-label="Social links">
    <span style="background:#2e6db3"></span><span style="background:#2aa0dc"></span><span style="background:#f2a21d"></span><span style="background:#c0392b"></span>
  </div>
</header>
<nav class="abs nav">
  <a class="active" style="left:90px">HOME</a>
  <a style="left:199px">ABOUT US</a>
  <a style="left:308px">SERVICES</a>
  <a style="left:414px">BLOG</a>
  <a style="left:491px">TESTIMONIALS</a>
  <a style="left:616px">CONTACT US</a>
</nav>
<section class="abs hero" role="img" aria-label="Greenhouse full of young cannabis plants in pots">
  <div class="abs hero-arrow" style="left:64px"><svg width="16" height="16" viewBox="0 0 16 16"><path d="M10 2 4 8l6 6" fill="none" stroke="#fff" stroke-width="2.4"/></svg></div>
  <div class="abs hero-arrow" style="left:733px"><svg width="16" height="16" viewBox="0 0 16 16"><path d="M6 2l6 6-6 6" fill="none" stroke="#fff" stroke-width="2.4"/></svg></div>
</section>
<main>
  <h1 class="abs welcome">Welcome to Our Site <b>Mainpage</b></h1>
  <p class="abs intro">Lorem ipsum dolor sit amet, consectetur adipiscing elit, sed do eiusmod tempor incididunt ut labore et dolore magna aliqua. Ut enim ad minim veniam, quis nostrud exercitation ullamco laboris nisi ut aliquip ex ea commodo consequat. Duis aute irure dolor in reprehenderit in voluptate velit esse cillum dolore eu fugiat nulla pariatur epteur sint occaecat cupidatat non.</p>
  <div class="abs btn">Read More</div>
  <div class="abs rule" style="top:628px"></div>

  <h2 class="abs section-title" style="top:658px">Our <b>Services</b></h2>
  <div class="abs pager" style="top:665px"><svg width="22" height="12" viewBox="0 0 22 12"><path d="M7 1 2 6l5 5" fill="none" stroke="#444" stroke-width="2.2"/><path d="M15 1l5 5-5 5" fill="none" stroke="#bbb" stroke-width="2.2"/></svg></div>
  <div class="abs service-img" style="left:91px;background:radial-gradient(ellipse 70px 45px at 50% 35%,rgba(190,140,110,.55),rgba(190,140,110,0)),radial-gradient(ellipse 90px 40px at 50% 100%,rgba(10,40,10,.7),rgba(10,40,10,0)),linear-gradient(135deg,#3f8f2a,#5aa83a 45%,#2a6a1c)" role="img" aria-label="Hands among green cannabis plants"></div>
  <div class="abs service-img" style="left:317px;background:radial-gradient(ellipse 80px 40px at 50% 95%,rgba(40,70,60,.6),rgba(40,70,60,0)),linear-gradient(135deg,#c9b548,#8a9a2a 40%,#d2b84e 70%,#7a8a30)" role="img" aria-label="Flowering yellow-green cannabis plants">
    <svg class="abs" style="left:78px;top:37px" width="46" height="46" viewBox="0 0 46 46"><circle cx="23" cy="23" r="23" fill="rgba(40,40,40,.6)"/><path d="M23 17v12M17 23h12" stroke="#fff" stroke-width="2.4"/></svg>
  </div>
  <div class="abs service-img" style="left:544px;background:radial-gradient(ellipse 60px 50px at 35% 40%,#a8d488,rgba(168,212,136,0)),radial-gradient(circle at 40% 40%,#7fb85c,#3f7f2a 70%,#2d5a1f)" role="img" aria-label="Close-up of a single cannabis leaf"></div>
  <h3 class="abs service-name" style="left:94px">NEQUE PORRO</h3>
  <h3 class="abs service-name" style="left:317px">DOLOREM IPSUM</h3>
  <h3 class="abs service-name" style="left:541px">CONSECTETUR ADIP</h3>
  <p class="abs service-text" style="left:94px">Duis aute irure dolor in reprehenderit in voluptate velit esse cillu.</p>
  <p class="abs service-text" style="left:317px">Duis aute irure dolor in reprehenderit in voluptate velit esse cillu.</p>
  <p class="abs service-text" style="left:544px">Duis aute irure dolor in reprehenderit in voluptate velit esse cillu.</p>
  <div class="abs rule" style="top:912px"></div>

  <h2 class="abs section-title" style="top:940px">Our <span class="accent">Blog</span> Post</h2>
  <div class="abs pager" style="top:945px"><svg width="22" height="12" viewBox="0 0 22 12"><path d="M7 1 2 6l5 5" fill="none" stroke="#444" stroke-width="2.2"/><path d="M15 1l5 5-5 5" fill="none" stroke="#bbb" stroke-width="2.2"/></svg></div>

  <article class="abs post" style="left:91px">
    <div class="abs avatar" role="img" aria-label="Author portrait"></div>
    <h4 class="abs post-title">Duis aute irure dolor</h4>
    <p class="abs post-text">reprehenderit in voluptate velit esse cillum dolore eu fugiat nulla pariatur epteur sint occaec.</p>
    <div class="abs post-meta">
      <span><svg width="9" height="9" viewBox="0 0 9 9"><rect x=".5" y="1.5" width="8" height="7" fill="none" stroke="#666"/><path d="M.5 3.5h8" stroke="#666"/></svg>March 14, 2014</span>
      <span><svg width="9" height="9" viewBox="0 0 9 9"><circle cx="4.5" cy="4.5" r="3.8" fill="none" stroke="#444" stroke-width="1.2"/><path d="M4.5 2.5v2h1.6" fill="none" stroke="#444"/></svg>8:28 PM</span>
    </div>
  </article>
  <article class="abs post" style="left:430px">
    <div class="abs avatar" role="img" aria-label="Author portrait"></div>
    <h4 class="abs post-title">Duis aute irure dolor</h4>
    <p class="abs post-text">reprehenderit in voluptate velit esse cillum dolore eu fugiat nulla pariatur epteur sint occaec.</p>
    <div class="abs post-meta">
      <span><svg width="9" height="9" viewBox="0 0 9 9"><rect x=".5" y="1.5" width="8" height="7" fill="none" stroke="#666"/><path d="M.5 3.5h8" stroke="#666"/></svg>March 14, 2014</span>
      <span><svg width="9" height="9" viewBox="0 0 9 9"><circle cx="4.5" cy="4.5" r="3.8" fill="none" stroke="#444" stroke-width="1.2"/><path d="M4.5 2.5v2h1.6" fill="none" stroke="#444"/></svg>8:28 PM</span>
    </div>
  </article>
</main>
<footer class="abs footer">
  <p class="abs copyright">Copyright ©2014. Yoursite. All Right Reserved</p>
  <div class="abs to-top"><svg class="abs" style="left:4px;top:4px" width="11" height="11" viewBox="0 0 11 11"><path d="M1.5 7.5 5.5 3.5l4 4" fill="none" stroke="#3b3b3b" stroke-width="2.2"/></svg></div>
</footer>
</body>
</html>
```